The Brandwell Firm

We need a new design for our letterhead and envelopes. We are a personal injury and criminal defense firm so we need something modern and clean, but more on the professional/traditional side. Our new logo has two colors and is attached to the file so we need something that works well with those colors/matches the design. The following information needs to be on the letterhead:
Phone: (555) 214-3370
Fax: (555) 214-5186
Toll-Free: (888) 431-2059
Post Office Box 4721
Millbrook, SC 29555-4721
HarmClaimCounsel.example
PalmettoTrialAdvocates.example

Target Market(s)

Clients, government agencies, other law firms

Industry/Entity Type

Legal

Font styles to use
Sans Serif
Other font styles liked:
• Arial

Colors

Designer to choose colors to be used in the design.

Requirements
Must have
• Must look professional and clean, modern
Nice to have
• I would like to see a design that works with the logo but does not distract from the content that will be printed on it
Should not have
• Too many colors or crazy designs.

```html
<!DOCTYPE html>
<html lang="en">
<head>
<meta charset="utf-8">
<title>The Brandwell Firm – Letterhead</title>
<link href="https://fonts.googleapis.com/css2?family=Lato:wght@300;400&family=Open+Sans:wght@400&display=swap" rel="stylesheet">
<style>
  :root {
    --brand-red: #d41f26;
    --brand-blue: #2e3192;
    --text-body: #4a4a4a;
    --text-dark: #333333;
    --rule: #8a8fc4;
    --backdrop: #e6e6e6;
    --paper: #ffffff;
  }
  * { margin: 0; padding: 0; box-sizing: border-box; }
  html, body {
    width: 1200px; height: 1200px; overflow: hidden;
    background: var(--backdrop);
  }
  .letterhead {
    position: absolute; left: 176px; top: 0;
    width: 847px; height: 1200px;
    background: var(--paper);
    font-family: "Lato", Arial, sans-serif;
    color: var(--text-body);
    overflow: hidden;
  }
  .brand {
    position: absolute; left: 54px; top: 112px;
    display: flex; align-items: center; gap: 12px;
  }
  .brand-mark { width: 14px; height: 14px; background: var(--brand-red); }
  .brand-name {
    font-family: "Lato", Arial, sans-serif;
    font-weight: 400; font-size: 31px; letter-spacing: 0.5px;
    color: var(--brand-blue);
  }
  .contact {
    position: absolute; left: 585px; top: 70px;
    border-left: 1.5px solid var(--rule);
    padding-left: 17px;
    font-family: "Open Sans", Arial, sans-serif;
    font-style: normal;
    font-size: 12.3px; line-height: 17.6px;
    color: var(--text-dark);
  }
  .contact .address { margin-bottom: 6px; }
  .contact ul { list-style: none; }
  .contact li { display: flex; align-items: center; gap: 5px; }
  .contact svg { width: 11px; height: 11px; flex: none; }
  .letter { position: absolute; left: 80px; top: 340px; width: 684px; }
  .salutation {
    font-size: 16.5px; font-weight: 400; color: var(--text-dark);
    margin-bottom: 26px;
  }
  .letter p.body {
    font-size: 16.3px; font-weight: 300; line-height: 27px;
    text-align: justify; hyphens: auto;
    margin-bottom: 26px;
  }
  .signature {
    width: 96px; height: 58px; margin-top: 64px;
    background: linear-gradient(120deg, #f1f1f1, #e2e2e2);
    border-radius: 3px;
  }
  .signer-name {
    margin-top: 34px; font-size: 22px; font-weight: 400; color: var(--text-dark);
  }
  .signer-title {
    margin-top: 10px; font-size: 15px; font-weight: 300; color: var(--text-body);
  }
  .footer-rule {
    position: absolute; left: 0; right: 0; bottom: 52px;
    height: 5px; background: var(--brand-red);
  }
  .footer-band {
    position: absolute; left: 0; right: 0; bottom: 0;
    height: 44px; background: var(--brand-blue);
  }
</style>
</head>
<body>
  <main class="letterhead">
    <header>
      <div class="brand">
        <span class="brand-mark"></span>
        <span class="brand-name">The Brandwell Firm</span>
      </div>
      <address class="contact">
        <div class="address">P.O.&nbsp; Box 4721 Millbrook,<br>SC 29555-4721</div>
        <ul>
          <li>
            <svg viewBox="0 0 12 12" aria-hidden="true"><path fill="var(--brand-red)" d="M2.5 1l2 2.3-1 1.2c.7 1.5 1.8 2.6 3.3 3.3l1.2-1 2.3 2-1.1 1.7C5 10.2 1.8 7 1 2.1z"/></svg>
            (555) 214-3370
          </li>
          <li>
            <svg viewBox="0 0 12 12" aria-hidden="true"><g fill="none" stroke="var(--brand-red)" stroke-width="1.3"><rect x="3" y="1.2" width="6" height="3"/><rect x="1" y="4.2" width="10" height="4.5"/><rect x="3" y="7" width="6" height="3.8"/></g></svg>
            (555) 214-5186
          </li>
          <li>
            <svg viewBox="0 0 12 12" aria-hidden="true"><path fill="var(--brand-red)" d="M2.5 1l2 2.3-1 1.2c.7 1.5 1.8 2.6 3.3 3.3l1.2-1 2.3 2-1.1 1.7C5 10.2 1.8 7 1 2.1z"/></svg>
            (888) 431-2059 (Toll-Free)
          </li>
          <li>
            <svg viewBox="0 0 12 12" aria-hidden="true"><g fill="none" stroke="var(--brand-red)" stroke-width="1"><circle cx="6" cy="6" r="5"/><ellipse cx="6" cy="6" rx="2.2" ry="5"/><path d="M1 6h10M2 3.3h8M2 8.7h8"/></g></svg>
            HarmClaimCounsel.example
          </li>
          <li>
            <svg viewBox="0 0 12 12" aria-hidden="true"><g fill="none" stroke="var(--brand-red)" stroke-width="1"><circle cx="6" cy="6" r="5"/><ellipse cx="6" cy="6" rx="2.2" ry="5"/><path d="M1 6h10M2 3.3h8M2 8.7h8"/></g></svg>
            PalmettoTrialAdvocates.example
          </li>
        </ul>
      </address>
    </header>

    <section class="letter">
      <p class="salutation">Dear Mr. Smith,</p>
      <p class="body">Lorem ipsum dolor sit amet, consectetur adipiscing elit. Donec orci purus, luctus vitae dignissim eu, iaculis sed purus. Vivamus faucibus, ipsum nec aliquet viverra, leo mauris condimentum ligula, sit amet sagittis enim ligula quis arcu. Nam egestas tortor id nisi porttitor mattis. In tortor ante, ultricies in suscipit a, tempus non massa. Vivamus et auctor mi. Fusce vel massa nulla. Phasellus nec eros mauris, et scelerisque orci. Donec malesuada orci vitae nulla accumsan porta a id massa. Quisque accumsan iaculis magna sit amet fringilla. Maecenas consequat, magna eget tincidunt semper, odio nibh rutrum mi, id feugiat ante nisi eu risus. Vestibulum nunc orci, rhoncus a placerat in, ultricies in mi. Cras mattis varius eros, vel fringilla nisi suscipit eget.</p>
      <p class="body">Quisque scelerisque sagittis nulla at porttitor. Mauris a justo et tellus interdum tristique. Sed id augue vitae urna euismod commodo aliquet a quam. Pellentesque arcu velit, cursus et malesuada ut, consequat et diam. Nullam erat sem, rhoncus id ullamcorper vitae, rhoncus et arcu. In ultricies ultricies nulla, ut rutrum nisi iaculis at. Donec eu magna a metus ornare faucibus. Fusce aliquet faucibus ultricies. Morbi semper, est id tincidunt gravida, sem arcu adipiscing lacus, ac bibendum nulla leo eu purus. Quisque nec diam sed risus consectetur a ccumsan quis quis nibh. Vestibulum id purus lorem.</p>
      <div class="signature" role="img" aria-label="Handwritten signature of the sender"></div>
      <p class="signer-name">John Doe</p>
      <p class="signer-title">Co-Founder &amp; CEO</p>
    </section>

    <footer>
      <div class="footer-rule"></div>
      <div class="footer-band"></div>
    </footer>
  </main>
</body>
</html>
```